DuePath.com website design

We are a collection agency that collects debt from past residents of apartments on behalf of Property Management Companies. We are want to design a 3 page website with - Home - How it Works - Schedule Demo. We'd like a sketch of a skyline showing high rise apartment buildings, houses, shops, etc. We would like for there to be some animation, possibly clouds and the sun slowly moving. Maybe kids playing ball or catch or something like that. Bird flying and landing. An electric car charging (to indicate we are modern). We are looking for a friendly community vibe. The site will also need a button "Property Managers Login". When some comes to the site we would like a pop up that says "Property Managers Click Here/Past Residents Click Here" with a different icon for each that relates to the description. I've included a link to a test site we had designed so feel free to use some of the copy from it. We just aren't happy with the design. On the Home page our tag line should be "Get more payments, faster, from past residents!" and "Digital First, NOT Digital Only". All without transaction fees, we don't get paid unless we get you paid first!
Additional selling points:

24 hour virtual agent and virtual telephone agent so we don't miss any opportunities to GET YOUR MONEY!

Old school collection strategies meet cutting edge technology to create effective work flow algorithms to put the best debt collectors on your accounts with data driven intelligence to determine the best way to get paid.

No Subscription Fees
No Payment Processing Fees
No Software Fees
No Mail, Email or TXT Fees

Inquire about our FIRST PARTY accounts receivable outsourcing. You may qualify for free post move out A/R processing and AI payment negotiator for the low hanging fruit. Don't pay full collection commission when there wasn't a full collection attempt!

For the How it Works page - See the page from our previous design. I will include the link below. Please come up with your own version of this but you can use the copy from this page.

The schedule demo page will be a form that will feed to our CRM that will include:
Name
Email
Company
Title
Phone Number
Number of Units
Tell us how we can help you: (a box for them provide details)

Also include our phone number at the bottom with something like

Here is a link to our previous design test site:
https://brookpreview.net/duepath-new/
I've attached an image of the back end so you can get an idea of the colors we need, I've also included our logo. For the most part we would like most of the site to match the blue colors from our logo, but we do need to incorporate some of the yellow in the images I've attached. Possibly make the buttons on the site the yellow color? Make the sun Match the yellow? I'll leave it up to you.

```html
<!DOCTYPE html>
<html lang="en">
<head>
<meta charset="utf-8">
<title>DuePath.com – Home</title>
<link href="https://fonts.googleapis.com/css2?family=Barlow:wght@500;600;700&family=Lato:wght@400;700&display=swap" rel="stylesheet">
<style>
:root{
  --navy:#1b3a6b;
  --cyan:#22b2d2;
  --yellow:#ffb81c;
  --board:#e6e6e6;
  --ink:#222;
  --soft:#f0fafc;
  --band:#1a4a88;
  --muted:#444;
}
*{margin:0;padding:0;box-sizing:border-box}
html,body{width:1200px;height:1152px;overflow:hidden;background:var(--board)}
.board{position:absolute;left:0;top:0;width:1960px;height:1882px;transform:scale(.6122);transform-origin:0 0;background:var(--board);font-family:'Lato',sans-serif;color:var(--ink)}
.page{position:absolute;top:47px;width:912px;height:1788px;background:#fff;overflow:hidden}
.page--popup{left:45px}
.page--plain{left:1003px}
.header{position:absolute;left:0;top:0;width:100%;height:55px}
.brand{position:absolute;display:flex;align-items:center;gap:8px;font-family:'Barlow',sans-serif;font-weight:600;color:var(--navy)}
.brand-dot{width:30px;height:30px;border-radius:50%;background:var(--cyan)}
.header .brand{left:102px;top:8px;font-size:30px}
.nav{position:absolute;top:20px;left:350px;display:flex;gap:34px;font-size:10.5px;font-weight:700;letter-spacing:.2px}
.nav a{color:#111;text-decoration:none}
.nav a.active{color:var(--cyan);border-bottom:2px solid var(--cyan);padding-bottom:4px}
.btn{display:inline-flex;align-items:center;justify-content:center;gap:5px;font-family:'Barlow',sans-serif;font-weight:600;color:#fff;border-radius:4px;text-decoration:none}
.btn--yellow{background:var(--yellow)}
.btn--teal{background:var(--cyan)}
.login{position:absolute;left:662px;top:10px;width:149px;height:35px;font-size:12.5px}
.hero-title{position:absolute;top:88px;width:100%;text-align:center;font-family:'Barlow',sans-serif;font-weight:700;font-size:28px;color:var(--navy)}
.hero-art{position:absolute;left:0;top:140px;width:100%;height:420px;background:linear-gradient(180deg,#fff 0%,#f4f4f4 40%,#ffd9a0 60%,#8fd3ec 78%,#fff 100%)}
.intro{position:absolute;top:572px;width:100%;text-align:center}
.h2{font-family:'Barlow',sans-serif;font-weight:700;font-size:32px;color:var(--navy)}
.h2 span{color:var(--cyan)}
.intro .lead{margin-top:14px;font-weight:700;font-size:12px;color:#111}
.intro .body{margin:14px auto 0;width:700px;font-size:10px;line-height:21px;color:var(--muted)}
.benefits{position:absolute;top:760px;left:0;width:100%;height:438px;background:var(--soft);text-align:center}
.benefits .h2{margin-top:56px}
.cards{position:absolute;top:120px;left:90px;display:flex;gap:0}
.card{width:183px}
.card-icon{width:96px;height:116px;margin:0 auto;border:14px solid var(--navy);border-right-color:var(--cyan);border-bottom-color:var(--cyan);border-radius:26px;display:flex;align-items:center;justify-content:center}
.card h3{margin-top:18px;font-family:'Barlow',sans-serif;font-weight:600;font-size:15px;line-height:21px;color:var(--navy)}
.card p{font-size:9.5px;line-height:21px;color:var(--muted)}
.cta{position:absolute;top:1198px;left:0;width:100%;height:326px;background:linear-gradient(120deg,#1f5a9c,#173f78 60%,#1c4d8c);text-align:center;color:#fff}
.cta h2{margin-top:58px;font-family:'Barlow',sans-serif;font-weight:600;font-size:25px;line-height:35px}
.cta h2 span{color:var(--cyan)}
.cta p{margin:12px auto 0;width:660px;font-size:10px;line-height:21px}
.cta .btn{margin-top:14px;width:107px;height:35px;font-size:12.5px}
.footer{position:absolute;top:1524px;left:0;width:100%;height:264px}
.footer .brand{left:117px;top:76px;font-size:30px}
.social{position:absolute;left:140px;top:133px;display:flex;gap:12px}
.social span{width:22px;height:22px;border-radius:50%;background:var(--navy)}
.fcol{position:absolute;top:56px;font-size:10px;color:var(--muted)}
.fcol h4{font-family:'Barlow',sans-serif;font-weight:600;font-size:12px;letter-spacing:.5px;color:#222;margin-bottom:6px}
.fcol li{list-style:none;line-height:21px}
.fcol li::before{content:"» ";color:#555}
.fcol.contact li::before{content:none}
.fcol.contact li{display:flex;gap:8px;align-items:flex-start}
.fcol.contact svg{flex:none;margin-top:5px}
.footer hr{position:absolute;left:60px;top:203px;width:792px;border:0;border-top:1px solid #bbb}
.copy{position:absolute;top:215px;width:100%;text-align:center;font-size:9.5px;color:#333}
.copy span{color:var(--cyan)}
.shade{position:absolute;inset:0;background:rgba(25,25,25,.62)}
.popup{position:absolute;left:100px;top:75px;width:711px;height:401px;background:#fff;border-radius:12px;overflow:hidden;text-align:center}
.popup-art{position:absolute;inset:0;background:linear-gradient(180deg,#f0f4f6 0%,#e4eef1 55%,#c6e6ef 78%,#fff 100%)}
.popup-body{position:relative;padding-top:116px}
.popup h1{font-family:'Barlow',sans-serif;font-weight:700;font-size:36px;color:var(--navy)}
.popup p{margin:4px auto 0;width:500px;font-size:10px;line-height:21px;color:#222}
.popup-actions{margin-top:14px;display:flex;justify-content:center;gap:13px}
.popup-actions .btn{height:36px;font-size:12px;padding:0 12px}
</style>
</head>
<body>
<div class="board">

<!-- Page state with entry popup -->
<section class="page page--popup">
  <header class="header">
    <div class="brand"><i class="brand-dot"></i>DuePath</div>
    <nav class="nav"><a class="active">HOME</a><a>HOW IT WORKS</a><a>SCHEDULE DEMO</a></nav>
    <a class="btn btn--yellow login">Property Managers Login</a>
  </header>
  <div class="hero-art" role="img" aria-label="Colourful city skyline illustration with houses, apartments, sun, cars and people"></div>
  <div class="intro">
    <h2 class="h2">Digital First, <span>NOT Digital Only</span></h2>
    <p class="lead">All without transaction fees, we don't get paid unless we get you paid first!</p>
    <p class="body">Lorem ipsum dolor sit amet, consectetur adipiscing elit, sed do eiusmod tempor incididunt ut labore et dolore magna aliqua. Ut enim ad minim veniam, quis nostrud exercitation ullamco laboris nisi ut aliquip ex ea commodo consequat. Duis aute irure dolor in reprehenderit in voluptate velit esse cillum dolore eu fugiat nulla pariatur. Excepteur sint occaecat cupidatat non proident, sunt in culpa qui officia deserunt mollit anim id est laborum.</p>
  </div>
  <div class="benefits">
    <h2 class="h2">Best Way <span>to Get Paid</span></h2>
    <div class="cards">
      <div class="card"><div class="card-icon"></div><h3>No Subscription<br>Fees</h3><p>Lorem ipsum dolor sit amet, consec-<br>tetur adipiscing elit, sed do eiusmod<br>tempor incididunt ut labore et<br>dolore magna aliqua.</p></div>
      <div class="card"><div class="card-icon"></div><h3>No Payment<br>Processing Fees</h3><p>Lorem ipsum dolor sit amet, consec-<br>tetur adipiscing elit, sed do eiusmod<br>tempor incididunt ut labore et<br>dolore magna aliqua.</p></div>
      <div class="card"><div class="card-icon"></div><h3>No Software<br>Fees</h3><p>Lorem ipsum dolor sit amet, consec-<br>tetur adipiscing elit, sed do eiusmod<br>tempor incididunt ut labore et<br>dolore magna aliqua.</p></div>
      <div class="card"><div class="card-icon"></div><h3>No Mail, Email or<br>TXT Fees</h3><p>Lorem ipsum dolor sit amet, consec-<br>tetur adipiscing elit, sed do eiusmod<br>tempor incididunt ut labore et<br>dolore magna aliqua.</p></div>
    </div>
  </div>
  <div class="cta">
    <h2>24 Hour Virtual Agent and Virtual<br>Telephone Agent So We Don't Miss Any Opportunities<br>to <span>GET YOUR MONEY!</span></h2>
    <p>Inquire about our FIRST PARTY accounts receivable outsourcing. You may qualify for free post move out A/R processing and AI payment negotiator for the low hanging fruit. Don't pay full collection commission when there wasn't a full collection attempt!</p>
    <a class="btn btn--yellow">Contact Us</a>
  </div>
  <footer class="footer">
    <div class="brand"><i class="brand-dot"></i>DuePath</div>
    <div class="social"><span></span><span></span><span></span><span></span></div>
    <div class="fcol" style="left:352px"><h4>LEGAL</h4><ul><li>Privacy Policy</li><li>Terms &amp; Conditions</li><li>About Us</li><li>Contact Us</li><li>FAQ</li></ul></div>
    <div class="fcol" style="left:503px"><h4>QUICK LINKS</h4><ul><li>Home</li><li>How It Works</li><li>Schedule Demo</li></ul></div>
    <div class="fcol contact" style="left:636px"><h4>CONTACT US</h4><ul>
      <li><svg width="8" height="11" viewBox="0 0 8 11"><path d="M4 0a4 4 0 0 1 4 4c0 3-4 7-4 7S0 7 0 4a4 4 0 0 1 4-4z" fill="#22b2d2"/></svg>123 Lorem ipsum dolor sit amet<br>consectetur adipiscing elit.</li>
      <li style="margin-top:6px"><svg width="9" height="9" viewBox="0 0 9 9"><path d="M1 0l2 2-1 1.5a6 6 0 0 0 3.5 3.5L7 6l2 2-1.5 1A8 8 0 0 1 0 1.5z" fill="#22b2d2"/></svg>+1 555 010 2040</li>
      <li style="margin-top:10px"><svg width="10" height="8" viewBox="0 0 10 8"><rect width="10" height="8" rx="1" fill="#22b2d2"/><path d="M0 1l5 3 5-3" stroke="#fff" fill="none"/></svg>hello@duepath-mail.com</li></ul></div>
    <hr>
    <p class="copy">© copyrights 2022 <span>DuePath</span> | &nbsp; All rights reserved.</p>
  </footer>
  <div class="shade"></div>
  <div class="popup">
    <div class="popup-art" role="img" aria-label="Soft sketched skyline with clouds, sun and row of buildings"></div>
    <div class="popup-body">
      <h1>Welcome To DuePath</h1>
      <p>Data driven intelligence meets unparalleled experience to deliver the most transparent, innovative and effective debt recovery.</p>
      <div class="popup-actions">
        <a class="btn btn--yellow"><svg width="11" height="11" viewBox="0 0 11 11"><circle cx="5.5" cy="3" r="3" fill="#fff"/><path d="M0 11a5.5 4.5 0 0 1 11 0z" fill="#fff"/></svg>Property Managers Click Here</a>
        <a class="btn btn--teal"><svg width="12" height="11" viewBox="0 0 12 11"><path d="M6 0l6 5h-2v6H2V5H0z" fill="#fff"/></svg>Past Residents Click Here</a>
      </div>
    </div>
  </div>
</section>

<!-- Page state without popup -->
<section class="page page--plain">
  <header class="header">
    <div class="brand"><i class="brand-dot"></i>DuePath</div>
    <nav class="nav"><a class="active">HOME</a><a>HOW IT WORKS</a><a>SCHEDULE DEMO</a></nav>
    <a class="btn btn--yellow login">Property Managers Login</a>
  </header>
  <h1 class="hero-title">Get More Payments, Faster, From Past Residents!</h1>
  <div class="hero-art" role="img" aria-label="Colourful city skyline illustration with houses, apartments, sun, cars and people"></div>
  <div class="intro">
    <h2 class="h2">Digital First, <span>NOT Digital Only</span></h2>
    <p class="lead">All without transaction fees, we don't get paid unless we get you paid first!</p>
    <p class="body">Lorem ipsum dolor sit amet, consectetur adipiscing elit, sed do eiusmod tempor incididunt ut labore et dolore magna aliqua. Ut enim ad minim veniam, quis nostrud exercitation ullamco laboris nisi ut aliquip ex ea commodo consequat. Duis aute irure dolor in reprehenderit in voluptate velit esse cillum dolore eu fugiat nulla pariatur. Excepteur sint occaecat cupidatat non proident, sunt in culpa qui officia deserunt mollit anim id est laborum.</p>
  </div>
  <div class="benefits">
    <h2 class="h2">Best Way <span>to Get Paid</span></h2>
    <div class="cards">
      <div class="card"><div class="card-icon"></div><h3>No Subscription<br>Fees</h3><p>Lorem ipsum dolor sit amet, consec-<br>tetur adipiscing elit, sed do eiusmod<br>tempor incididunt ut labore et<br>dolore magna aliqua.</p></div>
      <div class="card"><div class="card-icon"></div><h3>No Payment<br>Processing Fees</h3><p>Lorem ipsum dolor sit amet, consec-<br>tetur adipiscing elit, sed do eiusmod<br>tempor incididunt ut labore et<br>dolore magna aliqua.</p></div>
      <div class="card"><div class="card-icon"></div><h3>No Software<br>Fees</h3><p>Lorem ipsum dolor sit amet, consec-<br>tetur adipiscing elit, sed do eiusmod<br>tempor incididunt ut labore et<br>dolore magna aliqua.</p></div>
      <div class="card"><div class="card-icon"></div><h3>No Mail, Email or<br>TXT Fees</h3><p>Lorem ipsum dolor sit amet, consec-<br>tetur adipiscing elit, sed do eiusmod<br>tempor incididunt ut labore et<br>dolore magna aliqua.</p></div>
    </div>
  </div>
  <div class="cta">
    <h2>24 Hour Virtual Agent and Virtual<br>Telephone Agent So We Don't Miss Any Opportunities<br>to <span>GET YOUR MONEY!</span></h2>
    <p>Inquire about our FIRST PARTY accounts receivable outsourcing. You may qualify for free post move out A/R processing and AI payment negotiator for the low hanging fruit. Don't pay full collection commission when there wasn't a full collection attempt!</p>
    <a class="btn btn--yellow">Contact Us</a>
  </div>
  <footer class="footer">
    <div class="brand"><i class="brand-dot"></i>DuePath</div>
    <div class="social"><span></span><span></span><span></span><span></span></div>
    <div class="fcol" style="left:352px"><h4>LEGAL</h4><ul><li>Privacy Policy</li><li>Terms &amp; Conditions</li><li>About Us</li><li>Contact Us</li><li>FAQ</li></ul></div>
    <div class="fcol" style="left:503px"><h4>QUICK LINKS</h4><ul><li>Home</li><li>How It Works</li><li>Schedule Demo</li></ul></div>
    <div class="fcol contact" style="left:636px"><h4>CONTACT US</h4><ul>
      <li><svg width="8" height="11" viewBox="0 0 8 11"><path d="M4 0a4 4 0 0 1 4 4c0 3-4 7-4 7S0 7 0 4a4 4 0 0 1 4-4z" fill="#22b2d2"/></svg>123 Lorem ipsum dolor sit amet<br>consectetur adipiscing elit.</li>
      <li style="margin-top:6px"><svg width="9" height="9" viewBox="0 0 9 9"><path d="M1 0l2 2-1 1.5a6 6 0 0 0 3.5 3.5L7 6l2 2-1.5 1A8 8 0 0 1 0 1.5z" fill="#22b2d2"/></svg>+1 555 010 2040</li>
      <li style="margin-top:10px"><svg width="10" height="8" viewBox="0 0 10 8"><rect width="10" height="8" rx="1" fill="#22b2d2"/><path d="M0 1l5 3 5-3" stroke="#fff" fill="none"/></svg>hello@duepath-mail.com</li></ul></div>
    <hr>
    <p class="copy">© copyrights 2022 <span>DuePath</span> | &nbsp; All rights reserved.</p>
  </footer>
</section>

</div>
</body>
</html>
```